Pet Sitting Business Card

Would like a business card designed for my new pet sitting business
Card needs to match with logo design.
Blue and Orange are the theme colours.

Simple yet sophisticated design

company name:- MEADOWLARK PET CARE
Dana Kovich
Owner
0452716093
dana@meadowlarkpetcare.com.au
www.meadowlarkpetcare.com.au

I'm going to close my deadline early. I will be picking a winner by the 10th of May. Please submit designs before then.
thank you

Target Market(s)

All types of professional pet lovers wishing to have their pet looked after

Industry/Entity Type

Pet

Requirements
Must have
• Logo design
Blue and orange

```html
<!DOCTYPE html>
<html lang="en">
<head>
<meta charset="utf-8">
<title>Meadowlark Pet Care – Business Card</title>
<link href="https://fonts.googleapis.com/css2?family=Exo+2:wght@400;600;800&display=swap" rel="stylesheet">
<style>
  :root {
    --bg: #e9ecef;
    --card: #ffffff;
    --blue-deep: #1e8fe6;
    --blue-mid: #3ea6ef;
    --blue-light: #63d3e8;
    --orange: #f08a1c;
    --ink: #2b2b2b;
    --brand-blue: #2a7fd4;
  }
  * { box-sizing: border-box; margin: 0; padding: 0; }
  html, body {
    width: 1200px; height: 720px; overflow: hidden;
    background: var(--bg);
    font-family: "Exo 2", sans-serif;
  }
  .stage {
    position: relative; width: 1200px; height: 720px;
    display: flex; align-items: center; justify-content: center; gap: 50px;
  }
  .card {
    position: relative; width: 540px; height: 310px;
    background: var(--card); border-radius: 22px; overflow: hidden;
    box-shadow: 0 10px 30px rgba(0,0,0,0.15);
  }
  .card-wave { position: absolute; inset: 0; width: 100%; height: 100%; }
  .brand {
    position: absolute; display: flex; align-items: center; gap: 10px;
    color: var(--brand-blue); font-weight: 800; letter-spacing: 1px;
  }
  .brand-dot { width: 14px; height: 14px; border-radius: 50%; background: var(--orange); flex: none; }
  .brand-name { line-height: 1.05; text-align: center; }
  .tagline { position: absolute; color: var(--brand-blue); font-size: 11px; white-space: nowrap; }

  .card-front .brand { left: 0; right: 0; top: 175px; justify-content: center; font-size: 30px; }
  .card-front .tagline { left: 0; right: 0; top: 250px; text-align: center; }

  .card-back .brand { right: 34px; top: 130px; font-size: 28px; }
  .card-back .tagline { right: 60px; top: 204px; }

  .person { position: absolute; left: 30px; top: 46px; color: #fff; }
  .person-name { font-size: 17px; font-weight: 600; letter-spacing: 0.5px; }
  .person-role { font-size: 12px; letter-spacing: 0.5px; margin-top: 2px; }

  .address { position: absolute; left: 30px; top: 150px; font-size: 12px; color: var(--ink); line-height: 1.35; }
  .contacts { position: absolute; left: 30px; top: 198px; list-style: none; font-size: 11.5px; color: var(--ink); }
  .contacts li { display: flex; align-items: center; gap: 8px; height: 20px; }
  .contacts svg { width: 12px; height: 12px; fill: var(--blue-deep); flex: none; }
</style>
</head>
<body>
<main class="stage">

  <section class="card card-front" aria-label="Card front">
    <svg class="card-wave" viewBox="0 0 540 310" preserveAspectRatio="none" aria-hidden="true">
      <defs>
        <radialGradient id="frontGlow" cx="0.45" cy="0.2" r="0.75">
          <stop offset="0" stop-color="var(--blue-light)"/>
          <stop offset="0.6" stop-color="var(--blue-mid)"/>
          <stop offset="1" stop-color="var(--blue-deep)"/>
        </radialGradient>
      </defs>
      <path d="M0 0 H540 V95 C400 60 200 80 0 150 Z" fill="url(#frontGlow)"/>
    </svg>
    <div class="brand">
      <span class="brand-dot"></span>
      <span class="brand-name">MEADOWLARK<br>PET CARE</span>
    </div>
    <p class="tagline">Loving care for your furry friends</p>
  </section>

  <section class="card card-back" aria-label="Card back">
    <svg class="card-wave" viewBox="0 0 540 310" preserveAspectRatio="none" aria-hidden="true">
      <defs>
        <radialGradient id="backGlow" cx="0.5" cy="0.15" r="0.7">
          <stop offset="0" stop-color="var(--blue-light)"/>
          <stop offset="0.6" stop-color="var(--blue-mid)"/>
          <stop offset="1" stop-color="var(--blue-deep)"/>
        </radialGradient>
      </defs>
      <path d="M0 0 H540 V40 C380 55 180 90 0 140 Z" fill="url(#backGlow)"/>
      <path d="M0 140 C180 90 380 55 540 40 L540 46 C380 62 180 98 0 148 Z" fill="var(--orange)"/>
    </svg>

    <div class="person">
      <p class="person-name">DANA KOVICH</p>
      <p class="person-role">FINANCIAL ADVISOR</p>
    </div>

    <p class="address">041,6th floor,Harbour<br>Lane Road NTB</p>

    <ul class="contacts">
      <li><svg viewBox="0 0 24 24"><path d="M6.6 10.8a15 15 0 0 0 6.6 6.6l2.2-2.2a1 1 0 0 1 1-.25 11.4 11.4 0 0 0 3.6.57 1 1 0 0 1 1 1V20a1 1 0 0 1-1 1A17 17 0 0 1 3 4a1 1 0 0 1 1-1h3.5a1 1 0 0 1 1 1c0 1.25.2 2.45.57 3.57a1 1 0 0 1-.25 1z"/></svg>012 345 6789</li>
      <li><svg viewBox="0 0 24 24"><path d="M7 1h10a2 2 0 0 1 2 2v18a2 2 0 0 1-2 2H7a2 2 0 0 1-2-2V3a2 2 0 0 1 2-2zm0 3v14h10V4zm5 15.5a1 1 0 1 0 0 2 1 1 0 0 0 0-2z"/></svg>012 345 6789</li>
      <li><svg viewBox="0 0 24 24"><path d="M6 2h9v5H6zM3 8h18v10h-3v4H6v-4H3zm5 8v4h8v-4z"/></svg>012 345 6789</li>
      <li><svg viewBox="0 0 24 24"><path d="M2 5h20v14H2zm2 2v.5l8 5 8-5V7z"/></svg>urname@email.com</li>
      <li><svg viewBox="0 0 24 24"><path d="M12 2a10 10 0 1 0 0 20 10 10 0 0 0 0-20zm6.9 6h-3a15 15 0 0 0-1.3-3.9A8 8 0 0 1 18.9 8zM12 4a13 13 0 0 1 1.9 4h-3.8A13 13 0 0 1 12 4zM4.3 14a8 8 0 0 1 0-4h3.4a16 16 0 0 0 0 4zm.8 2h3a15 15 0 0 0 1.3 3.9A8 8 0 0 1 5.1 16zm3-8h-3a8 8 0 0 1 4.3-3.9A15 15 0 0 0 8.1 8zM12 20a13 13 0 0 1-1.9-4h3.8A13 13 0 0 1 12 20zm2.3-6H9.7a14 14 0 0 1 0-4h4.6a14 14 0 0 1 0 4zm.3 5.9a15 15 0 0 0 1.3-3.9h3a8 8 0 0 1-4.3 3.9zm1.7-5.9a16 16 0 0 0 0-4h3.4a8 8 0 0 1 0 4z"/></svg>www.urWebsitename.com</li>
    </ul>

    <div class="brand">
      <span class="brand-dot"></span>
      <span class="brand-name">MEADOWLARK<br>PET CARE</span>
    </div>
    <p class="tagline">Loving care for your furry friends</p>
  </section>

</main>
</body>
</html>
```